eBook Cover_H. Lindqvist-Borna
Schnell und zuverlässoig,Änderungswünsche wurden umgehend ausgeführt. Vielen Dank für das tolle Cover zu meinem ersten Buch!
Zielgruppe
freie Roman-Autorin (Erstlingswerk)
Zielgruppe: Lesende (Erwachsene), Frauen
Charakterisierung: magisch-realistischer Familienroman, spielt im Europa der Jetzt-Zeit
Aufgabenstellung
Im ersten Schritt geht es um ein Cover für ein eBook, das aber bei Bedarf als Book on Demand gedruckt werden soll. Es wird daher später Anforderung bzgl. Dicke / Umfang des gedruckten Buches und einer Rückseite geben. Das gewählte Design soll dann dahingehend überarbeitet und finale Druckdaten zur Verfügung gestellt werden. Dies soll von vornherein berücksichtigt werden und im Preis enthalten sein.
Titel: Regen über Glas, Monde im Moos
Autorinnenname: Henrike Lindqvist-Borna
des weiteren auf dem Cover: Roman

```html
<!DOCTYPE html>
<html lang="de">
<head>
<meta charset="utf-8">
<title>Regen über Glas, Monde im Moos – Henrike Lindqvist-Borna</title>
<link rel="stylesheet" href="https://fonts.googleapis.com/css2?family=Parisienne&family=Nunito+Sans:wght@800&family=PT+Sans&display=swap">
<style>
  :root {
    --stage: #dedede;
    --paper: #efefef;
    --ink: #666666;
    --ink-dark: #555555;
    --rule: #111111;
    --violet: #4c10c9;
    --ring: #a58be6;
    --meadow-deep: #5a7f3c;
    --meadow-light: #8fa845;
  }
  * { margin: 0; padding: 0; box-sizing: border-box; }
  html, body {
    width: 841px;
    height: 1200px;
    overflow: hidden;
    background: var(--stage);
  }
  .cover {
    position: absolute;
    left: 45px;
    top: 45px;
    width: 750px;
    height: 1108px;
    background: var(--paper);
    box-shadow: 4px 5px 8px rgba(0, 0, 0, 0.35);
    overflow: hidden;
  }
  .cover-art {
    position: absolute;
    inset: 0;
    width: 750px;
    height: 1108px;
  }
  .author {
    position: absolute;
    top: 78px;
    left: 0;
    width: 750px;
    text-align: center;
    font-family: "Parisienne", cursive;
    font-size: 44px;
    line-height: 1;
    color: var(--ink);
    letter-spacing: 1px;
  }
  .author-rule {
    position: absolute;
    top: 160px;
    left: 148px;
    width: 455px;
    height: 4px;
    background: var(--rule);
  }
  .title {
    position: absolute;
    top: 214px;
    left: 0;
    width: 750px;
    text-align: center;
    font-family: "Nunito Sans", sans-serif;
    font-weight: 800;
    font-size: 58px;
    line-height: 78px;
    color: var(--ink);
  }
  .title span { display: block; }
  .genre-badge {
    position: absolute;
    left: 221px;
    top: 626px;
    width: 308px;
    height: 308px;
    border-radius: 50%;
    background: #ffffff;
    border: 5px solid var(--ring);
    display: flex;
    align-items: center;
    justify-content: center;
    font-family: "PT Sans", sans-serif;
    font-size: 62px;
    color: var(--ink-dark);
    letter-spacing: 1px;
  }
</style>
</head>
<body>
  <div class="cover">
    <svg class="cover-art" viewBox="0 0 750 1108" xmlns="http://www.w3.org/2000/svg">
      <defs>
        <linearGradient id="meadow-tone" x1="0" y1="0" x2="0" y2="1">
          <stop offset="0" stop-color="var(--meadow-deep)"/>
          <stop offset="1" stop-color="var(--meadow-light)"/>
        </linearGradient>
      </defs>
      <polygon class="violet-wedge" points="0,384 750,662 0,911" fill="var(--violet)"/>
      <polygon class="meadow-painting" points="0,911 750,662 750,1108 0,1108"
               fill="url(#meadow-tone)" role="img"
               aria-label="Platz für ein Gemälde: Mohnblumenwiese vor blauem Hintergrund"/>
    </svg>

    <div class="author">Henrike Lindqvist-Borna</div>
    <div class="author-rule"></div>

    <h1 class="title">
      <span>Regen über Glas</span>
      <span>Monde im Moos</span>
    </h1>

    <div class="genre-badge">ROMAN</div>
  </div>
</body>
</html>
```